design a construction company business card

Design business card around our logo. Card must have all the typical info: name, title, address, phone, email, business name, etc. Somewhere on the card I would like to see our motto "Grounded in trust... Driven by honest craft." Consider adding a splash of bright orange to the card to complement the blues and silvers/grays in the logo. We are open to metallic inks, textures, etc. We would like to see options on both light and dark backgrounds. The font in the logo is Euro Technic Extended Regular.

```html
<!DOCTYPE html>
<html lang="en">
<head>
<meta charset="utf-8">
<title>Halden Contracting – Business Card</title>
<link rel="stylesheet" href="https://fonts.googleapis.com/css2?family=Michroma&family=Roboto+Condensed:ital,wght@1,700&display=swap">
<style>
  :root {
    --page-bg: #e9e6e1;
    --card-white: #ffffff;
    --card-mist: #e4e6e8;
    --blue-light: #2aa3dc;
    --blue-deep: #1f4fc0;
    --logo-blue: #1d63c9;
    --band-gray: #a9abae;
    --swoosh-gray: #c9cbce;
    --back-light: #8d8f92;
    --back-dark: #6a6c6f;
    --ink-white: #ffffff;
    --ink-soft: #eef1f4;
  }
  * { box-sizing: border-box; margin: 0; padding: 0; }
  html, body { width: 1200px; height: 780px; overflow: hidden; }
  body {
    background: var(--page-bg);
    font-family: "Michroma", sans-serif;
    position: relative;
  }
  .card {
    position: absolute;
    border-radius: 16px;
    overflow: hidden;
    box-shadow: 0 6px 18px rgba(0,0,0,.18);
  }

  /* Front card */
  .card-front {
    left: 130px; top: 105px;
    width: 330px; height: 570px;
    background: linear-gradient(180deg, var(--card-white) 0%, var(--card-mist) 45%);
  }
  .card-front .waves { position: absolute; inset: 0; width: 100%; height: 100%; }
  .front-brand {
    position: absolute; top: 150px; left: 0; width: 100%;
    text-align: center;
    color: var(--logo-blue);
    font-size: 15px; letter-spacing: .5px;
  }
  .identity {
    position: absolute; top: 305px; right: 26px;
    text-align: right; color: var(--ink-white);
  }
  .identity .name { font-size: 17px; letter-spacing: 1px; }
  .identity .title { font-size: 11px; margin-top: 4px; }
  .contact {
    position: absolute; top: 368px; left: 26px; right: 26px;
    color: var(--ink-white); font-size: 10.5px; line-height: 1.45;
  }
  .contact .label { display: block; text-align: right; font-size: 9px; }
  .contact .rule { height: 1px; background: rgba(255,255,255,.45); margin: 5px 0; }
  .contact .address { margin-top: 4px; }
  .website {
    position: absolute; bottom: 20px; left: 0; width: 100%;
    text-align: center; color: var(--ink-soft);
    font-size: 11px; letter-spacing: 1.5px;
  }

  /* Back card */
  .card-back {
    left: 530px; top: 225px;
    width: 570px; height: 330px;
    background: linear-gradient(160deg, var(--back-light) 0%, var(--back-dark) 100%);
  }
  .motto {
    position: absolute; top: 48px; left: 0; width: 100%;
    text-align: center;
    font-family: "Roboto Condensed", sans-serif;
    font-style: italic; font-weight: 700;
    color: var(--ink-soft); font-size: 15px; letter-spacing: .5px;
  }
  .back-brand {
    position: absolute; top: 150px; left: 0; width: 100%;
    text-align: center; color: var(--ink-white);
    font-size: 20px; letter-spacing: 1px;
  }
  .back-brand .mark {
    display: inline-block; width: 12px; height: 12px;
    background: var(--ink-white); margin-right: 12px; vertical-align: middle;
  }
</style>
</head>
<body>

<section class="card card-front" aria-label="Business card front">
  <svg class="waves" viewBox="0 0 330 570" preserveAspectRatio="none" aria-hidden="true">
    <defs>
      <linearGradient id="blueFill" x1="1" y1="0" x2="0" y2="1">
        <stop offset="0" stop-color="#2aa3dc"/>
        <stop offset="1" stop-color="#1f4fc0"/>
      </linearGradient>
    </defs>
    <path d="M0,262 Q150,212 330,228 L330,570 L0,570 Z" fill="#c9cbce"/>
    <path d="M0,282 Q160,236 330,250 L330,512 L0,512 Z" fill="url(#blueFill)"/>
    <path d="M70,292 Q200,270 300,300" fill="none" stroke="#ffffff" stroke-width="2" opacity=".85"/>
    <path d="M0,512 L330,512 L330,570 L0,570 Z" fill="#a9abae"/>
    <line x1="0" y1="515" x2="330" y2="515" stroke="#ffffff" stroke-width="2" opacity=".8"/>
  </svg>

  <div class="front-brand">Halden Contracting, Inc.</div>

  <div class="identity">
    <div class="name">ROWAN PIKE</div>
    <div class="title">Founder</div>
  </div>

  <div class="contact">
    <span class="label">Phone:</span>
    <div>(555) 014-2290</div>
    <div class="rule"></div>
    <span class="label">Email:</span>
    <div>hello@haldenbuild.com</div>
    <div class="rule"></div>
    <div class="address">PO Box 482 Quarry Lane<br>Eastfield</div>
  </div>

  <div class="website">www.HALDENBUILD.com</div>
</section>

<section class="card card-back" aria-label="Business card back">
  <p class="motto">Grounded in trust... Driven by honest craft.</p>
  <div class="back-brand"><span class="mark"></span>Halden Contracting, Inc.</div>
</section>

</body>
</html>
```